Stylish business cards for KV7

To create an appealing and professional business card design for a WOMEN Owned Construction Supply Company.
2 sided card. Incorporate brand elements, curvy, colorful, sleek and bright. No solid white background. attached samples of styles added shapes/ribbons. Want something with that WOW that looks awesome, factor. It is a new logo, so feel free to mess with logo colors in the blue and teal factors that can look good with both dark and light background. If you want to try a watermark with just the KV7, without the "Supply" that might look cool to.

Industry/Entity Type

Women owned construction supply company

Contact Information for Business Card

Name, Title, and phone number and email, web page. maybe spot for qr code.

Font styles to use
Sans Serif

Requirements
Nice to have
• would love to see colors, maybe stylish ribbon dividers or some sort of 2 or 3 tone color card that compliments logo.
Should not have
• Please do not have all white background. Do not include Home/reale state/ or building images.

```html
<!DOCTYPE html>
<html lang="en">
<head>
<meta charset="utf-8">
<title>KV7 Supply – Business Cards</title>
<link rel="stylesheet" href="https://fonts.googleapis.com/css2?family=Montserrat:wght@400;500;700&display=swap">
<style>
  :root {
    --backdrop: #1c1c1e;
    --navy: #1b3657;
    --teal: #2a91b8;
    --paper: #f4f4f4;
    --ink-light: #ffffff;
  }
  * { margin: 0; padding: 0; box-sizing: border-box; }
  html, body {
    width: 1200px; height: 1059px; overflow: hidden;
    background: var(--backdrop);
    font-family: "Montserrat", sans-serif;
  }
  .card {
    position: absolute;
    width: 690px; height: 392px;
    border-radius: 14px;
    background: var(--navy);
    overflow: hidden;
  }
  .card--front { left: 256px; top: 89px; }
  .card--back  { left: 255px; top: 547px; }

  .front-curve { position: absolute; inset: 0; }

  .identity { position: absolute; left: 32px; top: 133px; }
  .identity__name {
    color: var(--teal); font-weight: 700; font-size: 21px; letter-spacing: 0.3px;
  }
  .identity__title { color: var(--ink-light); font-size: 14px; margin-top: 2px; }

  .divider {
    position: absolute; left: 32px; width: 238px; height: 1px; background: var(--teal);
  }
  .divider--top { top: 194px; }
  .divider--bottom { top: 266px; }

  .address {
    position: absolute; left: 32px; top: 211px;
    color: var(--ink-light); font-size: 14.5px; line-height: 20px;
  }

  .contact { position: absolute; left: 32px; top: 283px; list-style: none; }
  .contact__item {
    display: flex; align-items: center; height: 28px;
    color: var(--ink-light); font-size: 14.5px;
  }
  .contact__icon { width: 13px; height: 13px; margin-right: 6px; flex: none; }

  .wordmark {
    position: absolute; font-weight: 700; white-space: nowrap;
    transform: translate(-50%, -50%);
  }
  .wordmark--front { left: 522px; top: 160px; font-size: 36px; color: var(--navy); }
  .wordmark--back  { left: 345px; top: 196px; font-size: 50px; color: var(--ink-light); }
</style>
</head>
<body>

<section class="card card--front" aria-label="Business card front">
  <svg class="front-curve" width="690" height="392" viewBox="0 0 690 392" aria-hidden="true">
    <path d="M222 0 C236 190 430 338 650 338" fill="none" stroke="var(--teal)" stroke-width="6"/>
    <path d="M232 0 C246 185 430 329 690 329 L690 0 Z" fill="var(--ink-light)" stroke="var(--ink-light)" stroke-width="3"/>
    <path d="M236 0 C250 182 432 328 690 328 L690 0 Z" fill="var(--paper)"/>
  </svg>

  <div class="wordmark wordmark--front">KV7 Supply</div>

  <div class="identity">
    <h1 class="identity__name">DANA WHITLOCK</h1>
    <p class="identity__title">CEO/Founder</p>
  </div>

  <div class="divider divider--top"></div>
  <p class="address">P.O Box 3170 Harbour Road Rise<br>Westbrook AB 40210</p>
  <div class="divider divider--bottom"></div>

  <ul class="contact">
    <li class="contact__item">
      <svg class="contact__icon" viewBox="0 0 24 24" aria-hidden="true"><path fill="var(--teal)" d="M6.6 10.8a15.1 15.1 0 0 0 6.6 6.6l2.2-2.2c.3-.3.7-.4 1-.2 1.1.4 2.3.6 3.6.6.6 0 1 .4 1 1V20c0 .6-.4 1-1 1A17 17 0 0 1 3 4c0-.6.4-1 1-1h3.5c.6 0 1 .4 1 1 0 1.3.2 2.5.6 3.6.1.3 0 .7-.2 1z"/></svg>
      435.555.0187
    </li>
    <li class="contact__item">
      <svg class="contact__icon" viewBox="0 0 24 24" aria-hidden="true"><path fill="var(--teal)" d="M2 5h20v14H2z"/><path d="M2 5l10 8 10-8" fill="none" stroke="var(--navy)" stroke-width="1.6"/></svg>
      info@kv7supply.com.au
    </li>
    <li class="contact__item">
      <svg class="contact__icon" viewBox="0 0 24 24" aria-hidden="true"><g fill="none" stroke="var(--teal)" stroke-width="1.8"><circle cx="12" cy="12" r="10"/><ellipse cx="12" cy="12" rx="4.5" ry="10"/><path d="M2 12h20M4 7h16M4 17h16"/></g></svg>
      www.kv7supply.com.au
    </li>
  </ul>
</section>

<section class="card card--back" aria-label="Business card back">
  <div class="wordmark wordmark--back">KV7 Supply</div>
</section>

</body>
</html>
```